Business Card Design (NEW FILES)

ATTENTION: New vector files are available. Please update your design to reflect/use the new (better resolution) logo images.

Seeking a unique and professional business card design for a commercial drone photography/videography business. The layout should feature
the logo (attached) and include the following information:
Owen Tarrick
614-502-7738
www.skylarkreelworks.example
NRD Certified Remote Pilot

Owen Tarrick

```html
<!DOCTYPE html>
<html lang="en">
<head>
<meta charset="utf-8">
<title>Skylark Reelworks Business Card</title>
<link href="https://fonts.googleapis.com/css2?family=Open+Sans:wght@400;600;700;800&display=swap" rel="stylesheet">
<style>
  :root {
    --backdrop: #222222;
    --navy: #1a1c4c;
    --navy-deep: #13163f;
    --white: #ffffff;
    --orange: #ee8a4d;
    --teal: #17b4b6;
    --card-w: 560px;
    --card-h: 340px;
  }
  * { margin: 0; padding: 0; box-sizing: border-box; }
  html, body {
    width: 1200px; height: 780px; overflow: hidden;
    background: var(--backdrop);
    font-family: "Open Sans", Arial, sans-serif;
  }
  .stage {
    width: 1200px; height: 780px;
    display: flex; align-items: center; justify-content: center; gap: 40px;
  }
  .card {
    position: relative;
    width: var(--card-w); height: var(--card-h);
    border-radius: 22px; overflow: hidden;
    box-shadow: 0 14px 30px rgba(0,0,0,0.45);
  }
  .card-front { background: var(--white); }
  .front-waves { position: absolute; inset: 0; width: 100%; height: 100%; }
  .brand {
    position: absolute; display: flex; align-items: center; gap: 10px;
    font-weight: 600; letter-spacing: 0.02em;
  }
  .brand-mark { border-radius: 50%; background: var(--orange); flex: none; }
  .card-front .brand { left: 38px; top: 40px; color: var(--navy); font-size: 24px; }
  .card-front .brand-mark { width: 18px; height: 18px; }
  .contact {
    position: absolute; right: 32px; top: 168px;
    text-align: right; color: var(--white);
  }
  .person-name { font-size: 27px; font-weight: 800; line-height: 1.1; letter-spacing: 0.01em; }
  .person-name .first { color: var(--orange); }
  .person-role { font-size: 14px; font-weight: 400; line-height: 1.3; }
  .credentials { font-size: 12.5px; margin-top: 6px; line-height: 1.45; }
  .contact-lines { list-style: none; margin-top: 6px; font-size: 12.5px; line-height: 1.6; }
  .contact-lines li { display: flex; justify-content: flex-end; align-items: center; gap: 8px; }
  .contact-lines svg { width: 13px; height: 13px; flex: none; }
  .card-back { background: var(--navy-deep); display: flex; align-items: center; justify-content: center; }
  .card-back .brand { position: static; color: var(--white); font-size: 34px; gap: 14px; }
  .card-back .brand-mark { width: 24px; height: 24px; }
</style>
</head>
<body>
<main class="stage">
  <section class="card card-front" aria-label="Business card front">
    <svg class="front-waves" viewBox="0 0 560 340" aria-hidden="true">
      <path d="M0,222 C90,272 210,217 330,147 C420,92 500,42 560,22" fill="none" stroke="var(--orange)" stroke-width="8"/>
      <path d="M0,238 C80,286 180,246 270,196" fill="none" stroke="var(--teal)" stroke-width="8"/>
      <path d="M0,250 C90,300 210,245 330,175 C420,120 500,70 560,50 L560,340 L0,340 Z" fill="var(--navy)"/>
    </svg>
    <div class="brand"><span class="brand-mark"></span>Skylark Reelworks</div>
    <div class="contact">
      <h1 class="person-name"><span class="first">Owen</span> Tarrick</h1>
      <p class="person-role">Owner</p>
      <p class="credentials">NRD Certified Remote Pilot<br>Fully Insured</p>
      <ul class="contact-lines">
        <li>614-502-7738
          <svg viewBox="0 0 24 24" aria-hidden="true"><path fill="var(--orange)" d="M6.6 10.8a15.1 15.1 0 0 0 6.6 6.6l2.2-2.2c.3-.3.7-.4 1-.2 1.1.4 2.3.6 3.6.6.6 0 1 .4 1 1V20c0 .6-.4 1-1 1A17 17 0 0 1 3 4c0-.6.4-1 1-1h3.5c.6 0 1 .4 1 1 0 1.3.2 2.5.6 3.6.1.3 0 .7-.2 1z"/></svg>
        </li>
        <li>www.skylarkreelworks.example
          <svg viewBox="0 0 24 24" aria-hidden="true"><circle cx="12" cy="12" r="10" fill="none" stroke="var(--orange)" stroke-width="2"/><path d="M2 12h20M12 2c3 3 3 17 0 20M12 2c-3 3-3 17 0 20" fill="none" stroke="var(--orange)" stroke-width="1.6"/></svg>
        </li>
      </ul>
    </div>
  </section>
  <section class="card card-back" aria-label="Business card back">
    <div class="brand"><span class="brand-mark"></span>Skylark Reelworks</div>
  </section>
</main>
</body>
</html>
```